Pinecrest Real Estate A5 Flyer

A5 Flyer for print distribution.

Front (include attached photo and branding):
Pinecrest are a new face in the Dunmore & Kelvinhurst real estate market. The Pinecrest team are both Dunmore ‘locals’ and are genuinely and sincerely committed to this community. They put people first and pursue exceptional outcomes for their clients. This is the founding vision of Pinecrest.

Values:
Outstanding Customer Service
Timely Communication
Integrity Always
People First
Exceptional Negotiation

If you’re thinking of selling, interested in a free market appraisal, or simply want to find out more about the Pinecrest team, please reach out to Trevor or Owen for a chat. We’d love to shout you a coffee at The Marigold Coffee + Kitchen.

Pinecrest Real Estate
E: hello@pinecrestrealestate-example.com.au
W: pinecrestrealestate-example.com.au

Back (half the page about Trevor, other half the page about Owen). Please include headshots (Owen is the younger one):

Owen Pritchard (Property Consultant):

Owen has an in-depth understanding of all things property & finance related. With a degree in property & finance, diploma in finance & mortgage broking, certificate IV in real estate practice, project management roles in residential property development, plus years of small business experience as co-founder/co-owner of The Marigold Coffee + Kitchen, his experience in managing competing demands and complex scenarios runs far and wide.

Owen also has experience in corporate negotiations which is proving to be a very beneficial skill set. Owen is deeply committed to people and pursuing exceptional outcomes for his clients. He has built a reputation as a man of his word who is genuine and sincere and willing to go above and beyond for his clients.

owen@pinecrestrealestate-example.com.au
0400 118 204

Trevor Bungey (Director / Licensee):

Trevor has worked in various roles inclusive of being a Real Estate Agent, Bank Manager, Financial Counsellor, Mortgage Broker, and previously a Commercial Pilot. He spent eight years in remote Western Australia, where he worked for an international mining company creating strategies to help support the well-being of employees. Trevor’s focus in life has always been to help people. To him, it is always about the relationship. Trevor gets enormous satisfaction from seeing individuals, families, and businesses thrive financially. He has become a skilled negotiator with extensive experience working for a number of corporations and private firms.
 
What differentiates Trevor is his compassion and commitment to people. He works hard to be an excellent communicator with the aim of achieving great results. He  has extensive sales experience with incredible ability to push the boundaries, think outside the box and meet or surpass expectations. This is why his clients keep coming back and continue to refer well into the future. 

trevor@pinecrestrealestate-example.com.au
0400 362 917

Target Market(s)

House Sellers / House Buyers

Industry/Entity Type

Real Estate

Colors
0054AA
0677BA
7BADD7
CADEEF
E8F1F8

Requirements
Must have
• Branding / logo, river photo, head shots, company details etc
Nice to have
• Design as per attached branding guide

```html
<!DOCTYPE html>
<html lang="en">
<head>
<meta charset="utf-8">
<title>Pinecrest Real Estate – A5 Flyer</title>
<link rel="stylesheet" href="https://fonts.googleapis.com/css2?family=Red+Hat+Display:wght@400;500;700;900&display=swap">
<style>
:root{
  --navy:#18222f;
  --paper:#e3e7eb;
  --white:#ffffff;
  --ink:#1b2431;
  --soft:#dfe4ea;
  --rule:#7d8796;
  --frame:#c7ced6;
  --board:#d9d9d9;
  --photo-top:#aeb8c2;
  --photo-mid:#4d6274;
  --photo-low:#2e4052;
}
*{box-sizing:border-box;margin:0;padding:0}
html,body{width:870px;height:1200px;overflow:hidden}
body{background:var(--board);font-family:"Red Hat Display",sans-serif;color:var(--ink);position:relative}

.flyer{position:absolute;top:290px;width:400px;height:566px;overflow:hidden;box-shadow:0 6px 18px rgba(0,0,0,.28)}
.flyer--front{left:25px;background:var(--navy)}
.flyer--back{left:445px}
.side-label{position:absolute;top:876px;width:400px;text-align:center;font-weight:900;font-size:28px;letter-spacing:.5px;color:#111}
.side-label--front{left:25px}
.side-label--back{left:445px}

/* FRONT */
.hero-photo{position:absolute;left:0;top:0;width:400px;height:283px;
  background:linear-gradient(180deg,var(--photo-top) 0%,#8d9aa6 14%,var(--photo-mid) 40%,var(--photo-low) 100%)}
.front-body{position:absolute;left:0;top:283px;width:400px;height:283px;padding:0 17px;border-top:2px solid var(--frame);color:var(--white);text-align:center}
.headline{font-weight:500;font-size:13.6px;line-height:13.8px;margin-top:13px}
.rule{height:1px;background:var(--rule);margin:6px 0 7px}
.intro{font-size:7.4px;line-height:9px;color:var(--soft);padding:0 8px}
.values{position:relative;border:1px solid var(--frame);margin-top:19px;height:62px;display:flex;align-items:center;padding:0 4px}
.values__title{position:absolute;left:50%;top:-11px;transform:translateX(-50%);background:var(--navy);border:1px solid var(--frame);padding:2px 10px;font-size:12px;font-weight:500;line-height:14px}
.value{flex:auto;font-size:8.4px;line-height:9.8px;font-weight:500;border-right:1px solid #8892a0;padding:9px 2px 0;height:46px;margin-top:4px}
.value:last-child{border-right:0}
.value__num{display:inline-block;width:13px;height:13px;border-radius:50%;background:var(--white);color:var(--navy);font-size:6.5px;font-weight:700;line-height:13px;margin-bottom:2px}
.closing{font-size:7.4px;line-height:9px;color:var(--soft);margin-top:11px;padding:0 2px}
.closing strong{font-weight:700;color:var(--white)}
.front-footer{display:flex;border-top:1px solid var(--rule);margin-top:6px;padding-top:6px;height:62px}
.brand{width:110px;border-right:1px solid var(--rule);margin-bottom:4px;display:flex;flex-direction:column;align-items:center;justify-content:center;gap:5px}
.brand__dot{width:26px;height:26px;border-radius:50%;background:var(--white)}
.brand__name{font-size:9px;font-weight:500;letter-spacing:3px;color:var(--white)}
.contacts{flex:1;padding-left:16px;text-align:left}
.contact{display:flex;align-items:center;gap:10px;height:26px;font-size:8.6px;letter-spacing:.4px;white-space:nowrap}
.contact + .contact{border-top:1px solid var(--rule)}
.contact b{font-weight:700}
.icon{width:18px;height:18px;flex:none;display:flex;align-items:center;justify-content:center;background:var(--white);color:var(--navy)}
.icon svg{width:12px;height:12px}

/* BACK */
.agent{position:absolute;left:0;width:400px;height:283px;padding:17px 18px 0}
.agent--light{top:0;background:var(--paper);color:var(--ink)}
.agent--dark{top:283px;background:var(--navy);color:var(--white)}
.agent__head{display:flex;width:218px;height:30px;border:1px solid currentColor}
.agent--dark .agent__head{border-color:var(--paper)}
.agent__name{background:var(--navy);color:var(--white);font-size:12.4px;font-weight:500;padding:0 7px;display:flex;align-items:center;width:107px;white-space:nowrap}
.agent--dark .agent__name{background:var(--paper);color:var(--ink)}
.agent__role{flex:1;font-size:9.2px;display:flex;align-items:center;padding-left:6px;letter-spacing:.2px;white-space:nowrap}
.agent__bio{width:219px;font-size:7.4px;line-height:9px;margin-top:10px}
.agent__bio p + p{margin-top:4px}
.agent--dark .agent__bio{color:var(--soft)}
.headshot{position:absolute;right:17px;top:17px;width:132px;height:213px;border:1px solid #5a6472;padding:2px}
.agent--dark .headshot{border-color:var(--frame)}
.headshot__fill{width:100%;height:100%;background:linear-gradient(180deg,#e6e4e0 0%,#d6d4d0 55%,#2f3e60 75%,#1f2a44 100%)}
.agent__contacts{position:absolute;left:18px;right:17px;bottom:17px;border-top:1px solid #8a94a1;padding-top:10px;display:flex;align-items:center;font-size:8.6px;letter-spacing:.4px;white-space:nowrap}
.agent__phone{display:flex;align-items:center;gap:10px;font-size:11.3px;font-weight:500;letter-spacing:.6px;padding-right:16px;border-right:1px solid #8a94a1;margin-right:16px;height:18px}
.agent__mail{display:flex;align-items:center;gap:8px}
.agent__mail b{font-weight:700}
.agent--light .icon{background:var(--navy);color:var(--white)}
</style>
</head>
<body>

<section class="flyer flyer--front">
  <div class="hero-photo" role="img" aria-label="Aerial photo of the river foreshore with suburban houses along the bank"></div>
  <div class="front-body">
    <h1 class="headline">Pinecrest are a new face in the Dunmore &amp; Kelvinhurst<br>real estate market</h1>
    <div class="rule"></div>
    <p class="intro">The Pinecrest team are both Dunmore ‘locals’ and are genuinely and sincerely committed to this community. They put people first and pursue exceptional outcomes for their clients. This is the founding vision of Pinecrest.</p>
    <div class="values">
      <span class="values__title">VALUES</span>
      <div class="value"><span class="value__num">01</span><br>Outstanding<br>Customer Service</div>
      <div class="value"><span class="value__num">02</span><br>People<br>First</div>
      <div class="value"><span class="value__num">03</span><br>Exceptional<br>Negotiation</div>
      <div class="value"><span class="value__num">04</span><br>Integrity<br>Always</div>
      <div class="value"><span class="value__num">05</span><br>Timely<br>Communication</div>
    </div>
    <p class="closing">If you’re thinking of selling, interested in a free market appraisal, or simply want to find out more about the Pinecrest team, please reach out to Trevor or Owen for a chat. We’d love to shout you a coffee at <strong>The Marigold Coffee + Kitchen</strong>.</p>
    <div class="front-footer">
      <div class="brand"><span class="brand__dot"></span><span class="brand__name">PINECREST</span></div>
      <div class="contacts">
        <div class="contact"><span class="icon"><svg viewBox="0 0 24 24" fill="none" stroke="currentColor" stroke-width="2"><rect x="3" y="5" width="18" height="14"/><path d="M3 5l9 8 9-8"/></svg></span><span>hello@<b>pinecrestrealestate-example</b>.com.au</span></div>
        <div class="contact"><span class="icon"><svg viewBox="0 0 24 24" fill="none" stroke="currentColor" stroke-width="2"><circle cx="12" cy="12" r="9"/><path d="M3 12h18M12 3c3 3 3 15 0 18M12 3c-3 3-3 15 0 18"/></svg></span><span>www.<b>pinecrestrealestate-example</b>.com.au</span></div>
      </div>
    </div>
  </div>
</section>

<section class="flyer flyer--back">
  <article class="agent agent--light">
    <div class="agent__head"><span class="agent__name">Trevor Bungey</span><span class="agent__role">Director / Licensee</span></div>
    <div class="agent__bio">
      <p>Trevor has worked in various roles inclusive of being a Real Estate Agent, Bank Manager, Financial Counsellor, Mortgage Broker, and previously a Commercial Pilot. He spent eight years in remote Western Australia, where he worked for an international mining company creating strategies to help support the well-being of employees. Trevor’s focus in life has always been to help people. To him, it is always about the relationship. Trevor gets enormous satisfaction from seeing individuals, families, and businesses thrive financially. He has become a skilled negotiator with extensive experience working for a number of corporations and private firms.</p>
      <p>What differentiates Trevor is his compassion &amp; commitment to people. He works hard to be an excellent communicator with the aim of achieving great results. He has extensive sales experience with incredible ability to push the boundaries, think outside the box and meet or surpass expectations. This is why his clients keep coming back and continue to refer well into the future.</p>
    </div>
    <div class="headshot"><div class="headshot__fill" role="img" aria-label="Headshot of Trevor Bungey in a navy suit"></div></div>
    <div class="agent__contacts">
      <span class="agent__phone"><span class="icon"><svg viewBox="0 0 24 24" fill="none" stroke="currentColor" stroke-width="2"><path d="M5 3h4l2 5-3 2a12 12 0 0 0 6 6l2-3 5 2v4a2 2 0 0 1-2 2A17 17 0 0 1 3 5a2 2 0 0 1 2-2z"/></svg></span>0400 362 917</span>
      <span class="agent__mail"><span class="icon"><svg viewBox="0 0 24 24" fill="none" stroke="currentColor" stroke-width="2"><rect x="3" y="5" width="18" height="14"/><path d="M3 5l9 8 9-8"/></svg></span><span>trevor@<b>pinecrestrealestate-example</b>.com.au</span></span>
    </div>
  </article>
  <article class="agent agent--dark">
    <div class="agent__head"><span class="agent__name">Owen Pritchard</span><span class="agent__role">Property Consultant</span></div>
    <div class="agent__bio">
      <p>Owen has an in-depth understanding of all things property and finance related. With a degree in property and finance, diploma in finance &amp; mortgage broking, certificate IV in real estate practice, project management roles in residential property development, plus years of small business experience as co-founder/co-owner of The Marigold Coffee + Kitchen, his experience in managing competing demands and complex scenarios runs far and wide.</p>
      <p>Owen also has experience in corporate negotiations which is proving to be a very beneficial skill set. Owen is deeply committed to people and pursuing exceptional outcomes for his clients. He has built a reputation as a man of his word who is genuine and sincere and willing to go above and beyond for his clients.</p>
    </div>
    <div class="headshot"><div class="headshot__fill" role="img" aria-label="Headshot of Owen Pritchard in a navy blazer"></div></div>
    <div class="agent__contacts">
      <span class="agent__phone"><span class="icon"><svg viewBox="0 0 24 24" fill="none" stroke="currentColor" stroke-width="2"><path d="M5 3h4l2 5-3 2a12 12 0 0 0 6 6l2-3 5 2v4a2 2 0 0 1-2 2A17 17 0 0 1 3 5a2 2 0 0 1 2-2z"/></svg></span>0400 118 204</span>
      <span class="agent__mail"><span class="icon"><svg viewBox="0 0 24 24" fill="none" stroke="currentColor" stroke-width="2"><rect x="3" y="5" width="18" height="14"/><path d="M3 5l9 8 9-8"/></svg></span><span>owen@<b>pinecrestrealestate-example</b>.com.au</span></span>
    </div>
  </article>
</section>

<div class="side-label side-label--front">FRONT</div>
<div class="side-label side-label--back">BACK</div>

</body>
</html>
```